Residential Remodeling Contractor needs updated business card

I need a new design for my business card.
Name of the company is Ridgefell Construction. I need a card that commands presence, strength, integrity. I have been in business for 28 years. I am a Residential Remodeling Contractor that covers all aspects of a residential remodel and build.

```html
<!DOCTYPE html>
<html lang="en">
<head>
<meta charset="utf-8">
<title>Ridgefell Construction – Business Card</title>
<link rel="stylesheet" href="https://fonts.googleapis.com/css2?family=Montserrat:wght@400;500;600&display=swap">
<style>
  :root {
    --backdrop: #3a3532;
    --card-blue: #213d7f;
    --ink: #ffffff;
    --ink-soft: rgba(255,255,255,0.82);
  }
  * { margin: 0; padding: 0; box-sizing: border-box; }
  html, body { width: 1200px; height: 786px; overflow: hidden; }
  body {
    background: var(--backdrop);
    font-family: "Montserrat", sans-serif;
    color: var(--ink);
    position: relative;
  }
  .card {
    position: absolute;
    top: 238px;
    width: 540px;
    height: 310px;
    background: var(--card-blue);
    box-shadow: 0 10px 28px rgba(0,0,0,0.45);
    overflow: hidden;
  }
  .card--front { left: 40px; }
  .card--back  { left: 620px; }

  .wordmark {
    font-weight: 500;
    text-transform: uppercase;
    letter-spacing: 0.06em;
    line-height: 1.05;
    color: var(--ink);
  }
  .wordmark .line { display: block; }

  .card--front .wordmark {
    position: absolute;
    top: 46px;
    right: 44px;
    font-size: 25px;
    text-align: left;
  }
  .card--front .wordmark .line + .line { padding-left: 20px; }

  .holder {
    position: absolute;
    left: 40px;
    bottom: 48px;
  }
  .holder__name { font-size: 22px; font-weight: 600; letter-spacing: 0.01em; }
  .holder__role { font-size: 13px; font-weight: 400; color: var(--ink-soft); margin-top: 4px; }

  .contact {
    position: absolute;
    left: 282px;
    top: 168px;
    font-size: 11.5px;
    font-weight: 400;
    list-style: none;
  }
  .contact__address { line-height: 1.35; margin-bottom: 16px; }
  .contact__item {
    display: flex;
    align-items: center;
    gap: 10px;
    margin-bottom: 9px;
  }
  .contact__item svg { width: 16px; height: 16px; flex: none; }

  .card--back { display: flex; align-items: center; justify-content: center; }
  .card--back .wordmark { font-size: 34px; }
  .card--back .wordmark .line + .line { padding-left: 28px; }
</style>
</head>
<body>
  <section class="card card--front" aria-label="Business card front">
    <div class="wordmark">
      <span class="line">Ridgefell</span>
      <span class="line">Construction</span>
    </div>

    <ul class="contact">
      <li class="contact__address">42 Cedar Hollow Lane<br>Brandon, MS 39042</li>
      <li class="contact__item">
        <svg viewBox="0 0 16 16" aria-hidden="true"><circle cx="8" cy="8" r="8" fill="#fff"/><path d="M5.2 4.2l1.6 1.6-.9 1.1c.5 1.1 1.3 1.9 2.4 2.4l1.1-.9 1.6 1.6-1 1.3C7.4 11.1 4.9 8.6 4 6l1.2-1.8z" fill="#213d7f"/></svg>
        555.014.2290
      </li>
      <li class="contact__item">
        <svg viewBox="0 0 16 16" aria-hidden="true"><rect x="1.5" y="3.5" width="13" height="9" rx="1" fill="#fff"/><path d="M2 4.2l6 4.6 6-4.6" fill="none" stroke="#213d7f" stroke-width="1.2"/></svg>
        info@ridgefellconstruction.com
      </li>
      <li class="contact__item">
        <svg viewBox="0 0 16 16" aria-hidden="true"><circle cx="8" cy="8" r="7" fill="#fff"/><g fill="none" stroke="#213d7f" stroke-width="1"><ellipse cx="8" cy="8" rx="3" ry="6.5"/><path d="M1.5 8h13M2.5 4.8h11M2.5 11.2h11"/></g></svg>
        www.ridgefellconstruction.com
      </li>
    </ul>

    <div class="holder">
      <p class="holder__name">Daniel Brooks</p>
      <p class="holder__role">Owner</p>
    </div>
  </section>

  <section class="card card--back" aria-label="Business card back">
    <div class="wordmark">
      <span class="line">Ridgefell</span>
      <span class="line">Construction</span>
    </div>
  </section>
</body>
</html>
```